Progressive Flow Chart

Looking for a progressive flow chart centered and branching off. They all build on each other 1-3. There will be 3 different pages.

Target Market(s)

Business Owners - High Net worth Individuals

Industry/Entity Type

Finance & Business Consulting

Font styles to use
Serif

Colors
0054AA
0677BA
7BADD7
CADEEF
E8F1F8
0094D4
00A9DD
6FCCEA
C7EBF8
E9F6FB
00AB8E
00BBA5
67D7C9
C6EFE9
E9F9F6

Requirements
Nice to have
• Clean, simple, and approachable.
Should not have
• Very Busy

```html
<!DOCTYPE html>
<html lang="en">
<head>
<meta charset="utf-8">
<title>Living Trust Flow Chart</title>
<link href="https://fonts.googleapis.com/css2?family=Ubuntu:wght@500;700&family=Open+Sans:wght@400;600&display=swap" rel="stylesheet">
<style>
  :root {
    --page: #f7f7f7;
    --navy: #0c1538;
    --navy-deep: #0a1233;
    --navy-light: #13265a;
    --blue: #2a9ee0;
    --teal: #00f5b4;
    --white: #ffffff;
    --ink: #0c1538;
    --muted: #4f7fb5;
  }
  html, body { margin: 0; width: 1200px; height: 1200px; overflow: hidden; background: var(--page); }
  .canvas { position: relative; width: 1200px; height: 1200px; display: flex; align-items: center; justify-content: center; }
  .chart { display: block; width: 1200px; height: 926px; }
  .heading { font-family: "Ubuntu", sans-serif; font-weight: 700; }
  .body-text { font-family: "Open Sans", sans-serif; font-weight: 600; fill: var(--white); }
  .node-title { font-size: 31px; fill: var(--blue); letter-spacing: 1px; }
  .node-sub { font-size: 20px; }
  .arrow-label { font-family: "Open Sans", sans-serif; font-weight: 600; font-size: 20px; fill: var(--white); letter-spacing: .5px; }
  .trust-name { font-size: 34px; font-weight: 700; fill: var(--ink); }
  .trust-sub { font-family: "Open Sans", sans-serif; font-weight: 600; font-size: 19px; fill: var(--ink); }
  .step-num { font-family: "Ubuntu", sans-serif; font-weight: 700; font-size: 40px; fill: var(--teal); }
  .badge-num { font-family: "Ubuntu", sans-serif; font-weight: 700; font-size: 40px; fill: var(--ink); }
  .flow { stroke: url(#flowGrad); stroke-width: 4; fill: none; }
  .box { fill: var(--navy-deep); stroke: url(#ringGrad); stroke-width: 5; }
  .brand-name { font-family: "Ubuntu", sans-serif; font-weight: 500; font-size: 56px; fill: #5cb5e8; }
  .brand-tag { font-family: "Ubuntu", sans-serif; font-weight: 500; font-size: 21px; fill: #5cb5e8; letter-spacing: 6px; }
</style>
</head>
<body>
<main class="canvas">
<svg class="chart" viewBox="95 293 1745 1347" xmlns="http://www.w3.org/2000/svg" role="img" aria-label="Progressive flow chart: living trust with you as trustee at the centre, branching to business, real estate, bank, insurance and charitable and gifting trusts">
  <defs>
    <linearGradient id="ringGrad" x1="0" y1="0" x2="1" y2="0">
      <stop offset="0" stop-color="#2a9ee0"/><stop offset="1" stop-color="#00f5b4"/>
    </linearGradient>
    <linearGradient id="flowGrad" gradientUnits="userSpaceOnUse" x1="180" y1="0" x2="1740" y2="0">
      <stop offset="0" stop-color="#2a9ee0"/><stop offset="1" stop-color="#19e6bd"/>
    </linearGradient>
    <linearGradient id="iconGrad" x1="0" y1="0" x2="1" y2="0">
      <stop offset="0" stop-color="#2a9ee0"/><stop offset="1" stop-color="#00f5b4"/>
    </linearGradient>
    <radialGradient id="bgGrad" cx=".5" cy=".3" r=".8">
      <stop offset="0" stop-color="#142a66"/><stop offset="1" stop-color="#0b1436"/>
    </radialGradient>
    <marker id="tip" viewBox="0 0 10 10" refX="9" refY="5" markerWidth="5" markerHeight="5" orient="auto">
      <path d="M0 0 L10 5 L0 10 Z" fill="#19e6bd"/>
    </marker>
    <path id="trustArc" d="M852 903 A140 140 0 0 1 1132 903"/>
  </defs>

  <rect class="background" x="95" y="293" width="1745" height="1347" fill="url(#bgGrad)"/>

  <!-- top connector -->
  <line x1="375" y1="494" x2="1557" y2="494" stroke="url(#flowGrad)" stroke-width="4"/>

  <!-- step 3 trusts -->
  <g class="trust-node">
    <path d="M290 570 A115 115 0 1 1 460 570" fill="none" stroke="#fff" stroke-width="3"/>
    <circle cx="375" cy="494" r="104" fill="#fff" stroke="url(#ringGrad)" stroke-width="18"/>
    <text class="heading trust-name" x="372" y="468" text-anchor="middle">CRT</text>
    <text class="trust-sub" x="374" y="498" text-anchor="middle">Charitable</text>
    <text class="trust-sub" x="376" y="522" text-anchor="middle">Remainder Trust</text>
    <path d="M373 545 L420 638 L373 618 L326 638 Z" fill="url(#iconGrad)" stroke="#0c1538" stroke-width="4" stroke-linejoin="round"/>
    <text class="badge-num" x="374" y="616" text-anchor="middle">3</text>
  </g>
  <g class="trust-node">
    <path d="M902 574 A115 115 0 1 1 1072 574" fill="none" stroke="#fff" stroke-width="3"/>
    <circle cx="987" cy="497" r="104" fill="#fff" stroke="url(#ringGrad)" stroke-width="18"/>
    <text class="heading trust-name" x="987" y="483" text-anchor="middle">DAF</text>
    <text class="trust-sub" x="987" y="511" text-anchor="middle">Donor Advise</text>
    <text class="trust-sub" x="987" y="535" text-anchor="middle">Funds</text>
    <path d="M985 548 L1032 642 L985 622 L938 642 Z" fill="url(#iconGrad)" stroke="#0c1538" stroke-width="4" stroke-linejoin="round"/>
    <text class="badge-num" x="986" y="620" text-anchor="middle">3</text>
  </g>
  <g class="trust-node">
    <path d="M1472 570 A115 115 0 1 1 1642 570" fill="none" stroke="#fff" stroke-width="3"/>
    <circle cx="1557" cy="494" r="104" fill="#fff" stroke="url(#ringGrad)" stroke-width="18"/>
    <text class="heading trust-name" x="1557" y="486" text-anchor="middle">GRAT'S &amp;</text>
    <text class="heading trust-name" x="1557" y="522" text-anchor="middle">IDGT'S</text>
    <path d="M1555 544 L1602 638 L1555 618 L1508 638 Z" fill="url(#iconGrad)" stroke="#0c1538" stroke-width="4" stroke-linejoin="round"/>
    <text class="badge-num" x="1556" y="614" text-anchor="middle">3</text>
  </g>

  <!-- flows -->
  <line class="flow" x1="770" y1="935" x2="550" y2="935" marker-end="url(#tip)"/>
  <text class="arrow-label" x="666" y="969" text-anchor="middle">INVEST</text>
  <line class="flow" x1="250" y1="1345" x2="250" y2="1036" marker-end="url(#tip)"/>
  <text class="arrow-label" transform="translate(232 1190) rotate(-90)" text-anchor="middle">INTEREST PAYMENTS</text>
  <line class="flow" x1="462" y1="1034" x2="462" y2="1345" marker-end="url(#tip)"/>
  <path d="M452 1170 L462 1188 L472 1170 Z" fill="#19e6bd"/>
  <text class="arrow-label" transform="translate(502 1197) rotate(-90)" text-anchor="middle">INVESTMENT</text>
  <line class="flow" x1="462" y1="1034" x2="915" y2="1340"/>
  <line class="flow" x1="780" y1="1249" x2="858" y2="1302" marker-end="url(#tip)"/>
  <line class="flow" x1="465" y1="1337" x2="882" y2="1100" marker-end="url(#tip)"/>
  <line class="flow" x1="540" y1="1294" x2="592" y2="1265" marker-end="url(#tip)"/>
  <text class="arrow-label" transform="translate(616 1305) rotate(-29)" text-anchor="middle">INCOME</text>
  <line class="flow" x1="1002" y1="1232" x2="1002" y2="1130" marker-end="url(#tip)"/>
  <text class="arrow-label" x="1082" y="1200" text-anchor="middle">INCOME</text>
  <line class="flow" x1="1160" y1="1053" x2="1490" y2="1277" marker-end="url(#tip)"/>
  <text class="arrow-label" transform="translate(1298 1188) rotate(34)" text-anchor="middle">MAKES PAYMENTS</text>
  <line class="flow" x1="1470" y1="1340" x2="1117" y2="1094" marker-end="url(#tip)"/>
  <text class="arrow-label" transform="translate(1263 1233) rotate(34)" text-anchor="middle">FUNDS TRUST</text>
  <line class="flow" x1="825" y1="1450" x2="550" y2="1450" marker-end="url(#tip)"/>
  <text class="arrow-label" x="682" y="1438" text-anchor="middle">PAYS RENT</text>

  <!-- living trust centre -->
  <g class="living-trust">
    <circle cx="992" cy="903" r="212" fill="#0c1538" stroke="url(#ringGrad)" stroke-width="22"/>
    <text class="heading" font-size="40" fill="#fff" letter-spacing="3">
      <textPath href="#trustArc" startOffset="50%" text-anchor="middle">LIVING TRUST</textPath>
    </text>
    <circle cx="994" cy="913" r="123" fill="url(#iconGrad)"/>
    <text class="heading" x="988" y="904" font-size="40" fill="#0c1538" text-anchor="middle">YOU</text>
    <text class="heading" x="988" y="946" font-size="40" fill="#0c1538" text-anchor="middle">TRUSTEE</text>
  </g>

  <!-- bank -->
  <g class="node bank">
    <rect class="box" x="186" y="850" width="355" height="180" rx="24"/>
    <path d="M275 850 A82 82 0 0 1 440 850" fill="none" stroke="#fff" stroke-width="2"/>
    <circle cx="357" cy="840" r="72" fill="#0c1538"/>
    <circle cx="357" cy="840" r="70" fill="url(#iconGrad)"/>
    <circle cx="353" cy="763" r="28" fill="#0c1538"/>
    <text class="step-num" x="353" y="778" text-anchor="middle">2</text>
    <g fill="#0c1538">
      <path d="M320 822 L357 802 L394 822 Z"/>
      <rect x="324" y="826" width="66" height="6"/>
      <rect x="329" y="836" width="10" height="30"/><rect x="352" y="836" width="10" height="30"/><rect x="375" y="836" width="10" height="30"/>
      <rect x="320" y="868" width="74" height="8"/>
    </g>
    <text class="heading node-title" x="357" y="951" text-anchor="middle">BANK</text>
    <text class="body-text node-sub" x="353" y="986" text-anchor="middle">Real estate + Businesses</text>
  </g>

  <!-- real estate -->
  <g class="node real-estate">
    <rect class="box" x="186" y="1347" width="355" height="180" rx="24"/>
    <path d="M275 1347 A82 82 0 0 1 440 1347" fill="none" stroke="#fff" stroke-width="2"/>
    <circle cx="357" cy="1337" r="72" fill="#0c1538"/>
    <circle cx="357" cy="1337" r="70" fill="url(#iconGrad)"/>
    <circle cx="353" cy="1260" r="28" fill="#0c1538"/>
    <text class="step-num" x="353" y="1275" text-anchor="middle">1</text>
    <g fill="none" stroke="#0c1538" stroke-width="5" stroke-linejoin="round">
      <path d="M320 1335 L357 1305 L394 1335"/>
      <path d="M330 1330 V1370 H384 V1330"/>
      <rect x="349" y="1348" width="16" height="22"/>
    </g>
    <text class="heading node-title" x="360" y="1446" text-anchor="middle">REAL ESTATE</text>
    <text class="body-text node-sub" x="356" y="1476" text-anchor="middle">Asset held in LLC</text>
  </g>

  <!-- business -->
  <g class="node business">
    <rect class="box" x="832" y="1347" width="355" height="178" rx="24"/>
    <path d="M921 1347 A82 82 0 0 1 1086 1347" fill="none" stroke="#fff" stroke-width="2"/>
    <circle cx="1003" cy="1337" r="72" fill="#0c1538"/>
    <circle cx="1003" cy="1337" r="70" fill="url(#iconGrad)"/>
    <circle cx="1001" cy="1272" r="28" fill="#0c1538"/>
    <text class="step-num" x="1001" y="1287" text-anchor="middle">1</text>
    <g fill="#0c1538">
      <rect x="968" y="1350" width="12" height="26"/><rect x="986" y="1340" width="12" height="36"/>
      <rect x="1004" y="1330" width="12" height="46"/><rect x="1022" y="1316" width="12" height="60"/>
    </g>
    <path d="M970 1336 L990 1326 L1008 1318 L1030 1300" fill="none" stroke="#0c1538" stroke-width="4"/>
    <text class="heading node-title" x="1007" y="1449" text-anchor="middle">BUSINESS</text>
    <text class="body-text" font-size="19" x="884" y="1480">LLC - MEMBER/MANAGER</text>
    <text class="body-text" font-size="19" x="884" y="1504">CORP = PRESIDENT</text>
  </g>

  <!-- insurance -->
  <g class="node insurance">
    <rect class="box" x="1385" y="1347" width="355" height="180" rx="24"/>
    <path d="M1474 1347 A82 82 0 0 1 1639 1347" fill="none" stroke="#fff" stroke-width="2"/>
    <circle cx="1557" cy="1337" r="72" fill="#0c1538"/>
    <circle cx="1557" cy="1337" r="70" fill="url(#iconGrad)"/>
    <circle cx="1555" cy="1264" r="28" fill="#0c1538"/>
    <text class="step-num" x="1555" y="1279" text-anchor="middle">2</text>
    <path d="M1557 1303 L1588 1314 V1340 C1588 1360 1574 1372 1557 1380 C1540 1372 1526 1360 1526 1340 V1314 Z" fill="none" stroke="#0c1538" stroke-width="5"/>
    <path d="M1543 1341 L1554 1352 L1573 1330" fill="none" stroke="#0c1538" stroke-width="5"/>
    <text class="heading node-title" x="1565" y="1445" text-anchor="middle">INSURANCE</text>
    <text class="body-text node-sub" x="1562" y="1474" text-anchor="middle">HELD IN ILIT</text>
    <text class="body-text node-sub" x="1562" y="1503" text-anchor="middle">Irrevocable Life Insurance Trust</text>
  </g>

  <!-- brand -->
  <g class="brand">
    <circle cx="1535" cy="880" r="60" fill="none" stroke="#5cb5e8" stroke-width="10"/>
    <text class="brand-name" x="1535" y="1068" text-anchor="middle">Harbor Vale</text>
    <text class="brand-tag" x="1535" y="1111" text-anchor="middle">ADVISORY</text>
  </g>
</svg>
</main>
</body>
</html>
```